A unique communication angle to crowdfunding

Looking for a fresh redesign of a crowd funding website that deals in real estate. I already have the content, but am looking to take the design to the next level.

Existing real estate crowd funding sites focus on the real estate. I want to explore communication angle that:
- puts the investor in the centre of the communication: "become a baron"
- highlights the international nature (international properties, international investors)

There's also quite a lot of copy on the site, as we need to explain the service in quite a bit of detail. There's room to reduce the copy and replace with graphics. Could also consider clicking to see different text (see our difference section in http://galleonfairs.com)

The backend of the platform is already being worked on by a specialist crowd funding service provider.

In total there are 5 pages to be designed.

The homepage is really important. Right now it looks quite dated. It doesn't have a great layout. Note there is no mobile version of the website, so the pages need to be seen well on mobile devices. When looking at the brief, refer to the following links too:

current website:
http://pennyduke.com

some revisions made so far:
http://preview.stakeharbor.com/7K3LQ9

Attached are logo files and another file which contained copy for the pages. No need to rework the logo.

Please make sure to use the same copy in the brief on the webpages, to ensure the layouts work. Designers are free to propose images they feel work on the pages.

I would like to see if rather than tweaking the pages, it's possible to come up with a better design concept. If the 5 pages are accepted, there's a chance I'll request an additional 4 pages.
Updates

Please note the font used in the logo is called "harabara" in case you decide to use it in any of the titles, etc.

Please note there is one additional page for which we would like to review designs. Note the page would be a template to be used on all future real estate detail pages. Here is an example of the current design for reference:

http://pennyduke.com/projects/view/14

In total there are 5 page designs required, (homepage + 4)

Thank you

FYI -

Just a quick note to give information from similar UK real estate crowdfunding sites:
http://www.housewalrus.co.uk
http://tiderock.co.uk
https://www.fundquarry.com

Of the above, only tiderock has a nice clean looking landing page. Information is clear and well laid out.

Hi all, just uploaded a new file in the brief. Contains some comments and a website reference. I thought it may help to explain how we could convey international aspect as well as how we could convey images in a more modern way. This is an option you can consider, but its entirely up to you how how answer the brief. Thanks!

Reason: As requested by some designers needing more time to complete their work. Continue to share your work in progress and receive timely feedback before the deadline.

We would like to let you know that we have just shortlisted the best designs. Together with that, we have also passed some detailed feedback to all designers who weren't shortlisted. If we didn't contact you, please let us know. If you haven't submitted a design or are working on revisions, please note these will no longer be taken into account now. We hope you understand that we need to close the project today. Thank you all once again for your great work and design concepts. Here's hoping we meet again on a future design brief. Cheers, pennyduke team.

Target Market(s)

At the moment, only rich are able to buy real estate. With this service, anyone can become a landlord. Target buyers:

Young professionals, looking to diversify from stock market and lower risk
People nearing retirement, looking for stable rental incomes
Retirees - looking to supplement pensions with possibility of capital gains
Parents - looking for a way to save long term for their children (instead of low interest paying bank accounts)

Industry/Entity Type

Communication

Font styles to use
Sans Serif
Other font styles liked:
• harabara

Colors
add136
f5f9eb
959595
000000

Requirements
Must have
• Overall, the site must convey "whoever you are, you too can become a landlord", and that you don't need to be wealthy to invest in real estate. See

Communication should put the investor (or the baron) at the centre. The investor can be any of those described in the target market.

Show the aspirational side of property ownership.

In addition to the investor/baron character, the second main theme is international. No other real estate crowdfunding website highlights this.
Nice to have
• Banner could show different consumer types, to illustrate that the service can appeal to many different profiles. Refer to attached file "home page reference - plainasbread.com" as an example of how this could be done.

Aim to show the international side of the service. Properties around the world, investors around the world.

```html
<!DOCTYPE html>
<html lang="en">
<head>
<meta charset="utf-8">
<title>pennyduke — Agents &amp; Developers</title>
<link href="https://fonts.googleapis.com/css2?family=Open+Sans:wght@400;600;700&family=Varela+Round&display=swap" rel="stylesheet">
<style>
:root{
  --green:#8dc63f;
  --ink:#4a4a4a;
  --text:#5a5a5a;
  --grey:#959595;
  --pale:#f7f7f7;
  --line:#d6d6d6;
  --charcoal:#4b4b4b;
  --white:#ffffff;
}
*{box-sizing:border-box;margin:0;padding:0}
html,body{width:680px;height:1200px;overflow:hidden;background:var(--white)}
body{font-family:"Open Sans",Arial,sans-serif;color:var(--text);font-size:7.7px;line-height:13.5px;position:relative}
.round{font-family:"Varela Round","Open Sans",sans-serif}

.site-header{position:absolute;top:0;left:0;width:680px;height:56px;border-bottom:1px solid #e4e4e4}
.brand{position:absolute;left:82px;top:15px;display:flex;align-items:center;gap:6px}
.brand-dot{width:22px;height:22px;border-radius:50%;background:var(--green)}
.brand-name{font-size:16px;font-weight:700;color:var(--green)}
.follow{position:absolute;left:351px;top:14px;display:flex;align-items:center;gap:6px;font-size:8px;color:var(--ink)}
.social{width:22px;height:16px;background:#d9d9d9}
.social.is-active{background:var(--green)}
.search{position:absolute;left:462px;top:13px;width:141px;height:16px;display:flex}
.search-field{flex:1;background:#eeeeee;font-size:6.5px;color:#999;padding:0 7px;line-height:16px}
.search-btn{width:22px;background:#5a5a5a;display:flex;align-items:center;justify-content:center}
.main-nav{position:absolute;right:76px;top:40px;display:flex;gap:14px;font-size:6.6px;color:#666;text-transform:uppercase}
.main-nav a{color:inherit;text-decoration:none;padding-bottom:6px}
.main-nav a.current{color:#333;font-weight:600;border-bottom:2px solid var(--green)}

.page-banner{position:absolute;left:77px;top:78px;width:526px;height:112px}
.banner-bar{height:5px;background:var(--green)}
.banner-body{position:relative;height:107px;background:#ebebeb;overflow:hidden}
.banner-city{position:absolute;right:0;top:0;width:275px;height:107px;background:linear-gradient(90deg,#ebebeb 0%,#c8c8c8 45%,#b3b3b3 100%)}
.banner-title{position:absolute;left:15px;top:42px;font-size:17px;font-weight:600;color:var(--ink)}

.section{position:absolute;left:0;width:680px;text-align:center}
.section-title{font-size:11.5px;color:var(--green);letter-spacing:-.1px}
.rule{width:336px;height:1px;background:var(--line);margin:6px auto 0}
.intro{top:222px}
.intro-copy{width:384px;margin:12px auto 0;text-align:left;font-size:7.5px}
.intro-copy p{margin-bottom:13.5px}
.hl{color:var(--green);font-weight:600}

.community{top:422px;height:300px;background:var(--pale);padding-top:27px}
.community-lead{width:430px;margin:8px auto 0;font-size:7.5px}
.steps{position:absolute;left:77px;top:103px;display:flex;gap:11px;text-align:left}
.step{width:168px}
.step-head{position:relative;height:34px;background:var(--green);border-radius:17px 0 0 17px;display:flex;align-items:center}
.step-icon{width:34px;height:34px;border-radius:50%;background:var(--charcoal);display:flex;align-items:center;justify-content:center}
.step-num{margin-left:10px;font-size:12px;color:var(--ink)}
.step-shade{height:4px;margin-left:30px;background:linear-gradient(90deg,transparent,#bdbdbd)}
.step-text{margin-top:7px;font-size:7.6px}
.section-divider{position:absolute;top:722px;left:0;width:680px;height:3px;background:#7a7a7a}

.incentives{top:750px}
.incentives-copy{width:424px;margin:8px auto 0;font-size:7.5px}

.skyline{position:absolute;left:0;top:852px;width:680px;height:76px;background:linear-gradient(180deg,#ffffff 0%,#c9c9c9 40%,#a6a6a6 100%)}
.footer-bar{position:absolute;left:0;top:928px;width:680px;height:39px;background:var(--charcoal)}
.footer-follow{position:absolute;left:77px;top:12px;display:flex;align-items:center;gap:8px;font-size:10px;color:var(--green)}
.footer-social{width:24px;height:17px;border:1px solid var(--green)}
.copyright{position:absolute;right:77px;top:13px;font-size:7.5px;color:var(--green)}

.legal{position:absolute;left:77px;top:982px;width:526px;font-size:7.7px;line-height:13.4px;color:var(--text)}
.legal p{margin-bottom:13.4px}
.group-mark{position:absolute;left:482px;top:985px;font-size:18px;color:#333;font-weight:600}
</style>
</head>
<body>

<header class="site-header">
  <div class="brand"><span class="brand-dot"></span><span class="brand-name">pennyduke</span></div>
  <div class="follow">Follow us on <span class="social is-active"></span><span class="social"></span></div>
  <div class="search">
    <div class="search-field">Search...</div>
    <div class="search-btn"><svg width="9" height="9" viewBox="0 0 10 10"><circle cx="4" cy="4" r="3" fill="none" stroke="#fff" stroke-width="1.4"/><line x1="6.2" y1="6.2" x2="9" y2="9" stroke="#fff" stroke-width="1.6"/></svg></div>
  </div>
  <nav class="main-nav">
    <a href="#">Home</a><a href="#">Sign in</a><a href="#" class="current">How it works</a><a href="#">Discover a project</a><a href="#">The duke blog</a><a href="#">Find out more</a>
  </nav>
</header>

<div class="page-banner">
  <div class="banner-bar"></div>
  <div class="banner-body">
    <div class="banner-city" role="img" aria-label="Grey city skyline of high-rise towers"></div>
    <h1 class="banner-title">Agents &amp; Developers</h1>
  </div>
</div>

<section class="section intro">
  <h2 class="section-title round">For agents looking for new buyers or developers raising funds.</h2>
  <div class="rule"></div>
  <div class="intro-copy">
    <p>It's free to list projects on <span class="hl">pennyduke</span>. Because we don't charge a fee, you retain all commissions payable by the seller you act for.</p>
    <p>In some cases we may also pay you an incentive for referring your own clients to invest in the properties you submit.</p>
    <p>For developers, we charge <span class="hl">2%</span> of the funds raised only where the project successfully achieves its funding target. If the target is not met, no funds are raised and no fee is payable.</p>
    <p>To submit a property or project <span class="hl">follow these instructions.</span></p>
  </div>
</section>

<section class="section community">
  <h2 class="section-title round">Reach a growing investing community keen to buy real estate.</h2>
  <div class="rule"></div>
  <p class="community-lead">We only accept proposals from experienced developers and leading estate agents. New projects will be listed for free if they can be shown to be attractive to the community.</p>
  <div class="steps">
    <div class="step">
      <div class="step-head"><span class="step-icon"><svg width="14" height="16" viewBox="0 0 14 16"><rect x="2" y="1" width="9" height="14" rx="1" fill="none" stroke="#fff" stroke-width="1.3"/><line x1="4" y1="5" x2="9" y2="5" stroke="#8dc63f" stroke-width="1.2"/><line x1="4" y1="8" x2="9" y2="8" stroke="#fff" stroke-width="1"/></svg></span><span class="step-num round">One</span></div>
      <div class="step-shade"></div>
      <p class="step-text">Fill in the project submission form, ensuring you include all relevant details. Provide estimates of the potential rental income and include relevant benchmarks for similar properties in the same area. Note the purchase or investment must be possible by a UK limited company.</p>
    </div>
    <div class="step">
      <div class="step-head"><span class="step-icon"><svg width="16" height="14" viewBox="0 0 16 14"><rect x="1" y="3" width="11" height="9" fill="none" stroke="#fff" stroke-width="1.3"/><line x1="6" y1="9" x2="14" y2="1" stroke="#8dc63f" stroke-width="1.6"/></svg></span><span class="step-num round">Two</span></div>
      <div class="step-shade"></div>
      <p class="step-text"><b>Pennyduke</b> will review the submission with you to better understand the property and gauge its potential to be crowd funded among the community. We prepare the listing based on your materials.</p>
    </div>
    <div class="step">
      <div class="step-head"><span class="step-icon"><svg width="14" height="16" viewBox="0 0 14 16"><rect x="2" y="2" width="10" height="13" rx="1" fill="none" stroke="#fff" stroke-width="1.3"/><polyline points="4.5,9 6.5,11 10,6.5" fill="none" stroke="#8dc63f" stroke-width="1.5"/></svg></span><span class="step-num round">Three</span></div>
      <div class="step-shade"></div>
      <p class="step-text">Once the project is listed on the website, follow the funding progress in real time. As soon as the funding target is reached we will take care of all the administration and complete the purchase through you, on behalf of the community and your seller.</p>
    </div>
  </div>
</section>
<div class="section-divider"></div>

<section class="section incentives">
  <h2 class="section-title round">Additional incentives that reward you</h2>
  <div class="rule"></div>
  <p class="incentives-copy">Ask about the referrers scheme that rewards you for introducing buyers from your existing client base who may not be able to purchase alone and wish to purchase as part of a community.</p>
</section>

<div class="skyline" role="img" aria-label="Grey silhouette of world city landmarks"></div>

<footer class="footer-bar">
  <div class="footer-follow">Follow us on <span class="footer-social"></span><span class="footer-social"></span></div>
  <div class="copyright">© pennyduke 2014</div>
</footer>

<div class="group-mark">sprout capital</div>
<div class="legal">
  <p><span class="hl">Penny Duke</span> is part of the Sprout Capital Group. The Sprout Capital Group is a worldwide pioneer and<br>leader in the crowd investing, peer to peer and online investment market.</p>
  <p>By accessing this site and any pages thereof, you agree to be bound by the terms and conditions. This website is only suitable, intended and available for professional or sophisticated, or similar investors in other jurisdictions, or those who are members of pennyduke community and familiar with, and willing to, accept the risks associated with private participation. Pennyduke does not endorse any of the projects that appear on this website, nor does it make any recommendations regarding the appropriateness of particular opportunities for any participant. Each potential participant must review and evaluate the projects in his or her own discretion and determine the suitability of participating.</p>
  <p>This website (the "Site") is in every respect unaffiliated with any site to which it links or to any company or entity (and connected projects, investment opportunity or similar) featured on this Site, and is not meant as an endorsement of any of those companies or entities ("third parties"). Furthermore and for the avoidance of doubt, Pennyduke Limited is in no way affiliated with any third parties featured or referenced on this Site. There is no commercial relationship between Pennyduke Limited and such third parties, nor an agency arrangement or similar. If you believe your Content (including third party content) as each such term is defined in our Terms of Service has been reproduced on the Site without permission, please refer to our Terms of Service for information on how to request its removal from the Site.</p>
</div>

</body>
</html>
```